Hall of Fame annnouncement graphic for social media

I need a social media Hall of Fame announcement designed in the styles of some of the examples I've posted. I have attached the two gentlemens head shots ... the names are Dale Brinton and Ray Pemberly

It is for the BRAXWOOD LINKS HONOR GALLERY also include 2026 Inductees ... I have also attached the logo... make the post in similar colors as the logo.

I need this tomorrow so I am going to pick a winner in the next 24 hours.

```html
<!DOCTYPE html>
<html lang="en">
<head>
<meta charset="utf-8">
<title>Braxwood Links Honor Gallery – 2026 Inductees</title>
<link rel="stylesheet" href="https://fonts.googleapis.com/css2?family=Open+Sans:wght@500;700&family=Montserrat:wght@900&family=Oswald:wght@700&family=Roboto:wght@700&family=Anton&display=swap">
<style>
  :root {
    --royal: #0a2a86;
    --royal-deep: #061d63;
    --royal-mid: #1b3f9e;
    --red: #b01c12;
    --white: #ffffff;
    --frame: #3a3f4a;
    --photo-light: #e4e4e4;
    --photo-mid: #bfc3cc;
  }
  * { margin: 0; padding: 0; box-sizing: border-box; }
  html, body {
    width: 1200px; height: 728px; overflow: hidden;
    background: var(--royal);
  }
  .post {
    position: relative; width: 1200px; height: 728px; overflow: hidden;
    background: var(--royal);
    color: var(--white);
  }
  .crowd-backdrop {
    position: absolute; inset: 0;
    background:
      radial-gradient(ellipse at 20% 75%, rgba(40,80,180,0.55), transparent 55%),
      radial-gradient(ellipse at 80% 85%, rgba(40,80,180,0.45), transparent 50%),
      linear-gradient(180deg, var(--royal) 0%, var(--royal-mid) 60%, var(--royal-deep) 100%);
  }
  .brand-name {
    position: absolute; left: 60px; top: 116px; width: 460px;
    font-family: "Open Sans", sans-serif; font-weight: 700;
    font-size: 40px; line-height: 1.15; letter-spacing: 1px;
    text-align: center; color: var(--white);
  }
  .headline-lead {
    position: absolute; left: 64px; top: 316px;
    font-family: "Open Sans", sans-serif; font-weight: 500;
    font-size: 60px; line-height: 1; letter-spacing: -0.5px;
  }
  .headline-band {
    position: absolute; left: 50px; top: 408px; width: 440px; height: 121px;
    background: var(--red); border-radius: 20px 0 0 20px;
    display: flex; align-items: center; padding-left: 40px;
    font-family: "Montserrat", sans-serif; font-weight: 900;
    font-size: 78px; letter-spacing: 2px;
  }
  .year { position: absolute; left: 62px; top: 560px; width: 192px; height: 100px; }
  .year text {
    font-family: "Oswald", sans-serif; font-weight: 700;
    font-size: 118px; fill: var(--white);
  }
  .inductees { position: absolute; left: 268px; top: 560px; width: 195px; }
  .star-row { display: block; width: 195px; height: 22px; }
  .inductees-label {
    font-family: "Open Sans", sans-serif; font-weight: 500;
    font-size: 40px; line-height: 1.25; letter-spacing: -0.3px;
  }
  .headshot {
    position: absolute; top: 87px; width: 268px; height: 313px;
    border: 2px solid var(--frame); border-bottom: none;
    background: linear-gradient(180deg, var(--photo-light) 0%, var(--photo-mid) 62%, rgba(120,140,200,0.6) 85%, rgba(10,42,134,0) 100%);
  }
  .headshot--left { left: 559px; }
  .headshot--right { left: 838px; }
  .name-tag {
    position: absolute; top: 321px; height: 48px;
    background: var(--red);
    font-family: "Roboto", sans-serif; font-weight: 700;
    font-size: 26px; line-height: 48px; white-space: nowrap;
  }
  .name-tag--left { left: 559px; width: 192px; padding-left: 8px; border-radius: 0 24px 24px 0; }
  .name-tag--right { left: 925px; width: 181px; padding-left: 18px; border-radius: 24px 0 0 24px; }
  .headline-outline { position: absolute; left: 483px; top: 402px; width: 670px; height: 260px; }
  .headline-outline text {
    font-family: "Anton", sans-serif; font-size: 300px;
    fill: var(--royal); stroke: var(--white); stroke-width: 4;
  }
</style>
</head>
<body>
  <main class="post">
    <div class="crowd-backdrop" role="img" aria-label="Faded blue-toned photograph of a historic golf gallery crowd"></div>

    <div class="brand-name">BRAXWOOD LINKS<br>HONOR GALLERY</div>

    <div class="headshot headshot--left" role="img" aria-label="Headshot of Ray Pemberly"></div>
    <div class="headshot headshot--right" role="img" aria-label="Headshot of Dale Brinton"></div>
    <div class="name-tag name-tag--left">Ray Pemberly</div>
    <div class="name-tag name-tag--right">Dale Brinton</div>

    <div class="headline-lead">Braxwood Links</div>
    <div class="headline-band">HONOR</div>

    <svg class="headline-outline" viewBox="0 0 670 260" aria-label="GALLERY">
      <text x="4" y="254" textLength="662" lengthAdjust="spacingAndGlyphs">GALLERY</text>
    </svg>

    <svg class="year" viewBox="0 0 192 100" aria-label="2026">
      <text x="0" y="98" textLength="190" lengthAdjust="spacingAndGlyphs">2026</text>
    </svg>
    <div class="inductees">
      <svg class="star-row" viewBox="0 0 195 22" aria-hidden="true">
        <defs>
          <polygon id="star" points="10,1 12.4,7.8 19.5,7.8 13.8,12 16,19 10,14.7 4,19 6.2,12 0.5,7.8 7.6,7.8" fill="#ffffff"/>
        </defs>
        <use href="#star" x="0"/><use href="#star" x="22"/><use href="#star" x="44"/>
        <use href="#star" x="66"/><use href="#star" x="88"/><use href="#star" x="110"/>
        <use href="#star" x="132"/><use href="#star" x="154"/><use href="#star" x="175"/>
      </svg>
      <div class="inductees-label">Inductees</div>
      <svg class="star-row" viewBox="0 0 195 22" aria-hidden="true">
        <use href="#star" x="0"/><use href="#star" x="22"/><use href="#star" x="44"/>
        <use href="#star" x="66"/><use href="#star" x="88"/><use href="#star" x="110"/>
        <use href="#star" x="132"/><use href="#star" x="154"/><use href="#star" x="175"/>
      </svg>
    </div>
  </main>
</body>
</html>
```